Business Card for Industrial Distributor

We need a business card design for an industrial distributor. We sell machine parts for the manufacturing and oil industry. We would like the cards to look clean and modern but with a touch of industry.

Our colors are blue/white.

Please feel free to visit our website www.korvelpartsco.com

Target Market(s)

mexican manufacturers in the automobile/aerospace industry

Industry/Entity Type

Industrial

Colors
ffffff
0555a3

```html
<!DOCTYPE html>
<html lang="en">
<head>
<meta charset="UTF-8">
<title>Korvel Business Card</title>
<link href="https://fonts.googleapis.com/css2?family=Montserrat:wght@400;500;700;800&display=swap" rel="stylesheet">
<style>
  :root {
    --bg: #2b2b2d;
    --brand-blue: #1178c4;
    --navy: #25309a;
    --white: #ffffff;
    --text-blue: #2a6fc0;
  }
  * { box-sizing: border-box; margin: 0; padding: 0; }
  html, body { width: 1200px; height: 900px; overflow: hidden; }
  body {
    background: var(--bg);
    font-family: "Montserrat", sans-serif;
    display: flex;
    align-items: center;
    justify-content: center;
    gap: 40px;
  }
  .card {
    position: relative;
    width: 540px;
    height: 310px;
    border-radius: 18px;
    overflow: hidden;
  }
  .card-shapes { position: absolute; inset: 0; width: 100%; height: 100%; }

  /* Back side */
  .card-back { background: var(--brand-blue); }
  .back-mark {
    position: absolute;
    left: 50%; top: 118px;
    transform: translate(-50%, -50%);
    display: flex; flex-direction: column; align-items: center; gap: 12px;
  }
  .back-mark-dot {
    width: 130px; height: 130px; border-radius: 50%;
    background: var(--white);
  }
  .back-mark-name {
    color: var(--white); font-weight: 700; font-size: 26px; letter-spacing: 1px;
  }
  .back-web {
    position: absolute; left: 26px; bottom: 14px;
    color: var(--navy); font-size: 15px; font-weight: 500;
  }
  .back-web strong { color: var(--brand-blue); font-weight: 700; }

  /* Front side */
  .card-front { background: var(--white); }
  .brand {
    position: absolute; left: 26px; top: 86px;
    display: flex; align-items: center; gap: 12px;
  }
  .brand-dot { width: 56px; height: 56px; border-radius: 50%; background: var(--navy); }
  .brand-name { color: var(--navy); font-weight: 800; font-size: 54px; letter-spacing: -1px; }
  .person {
    position: absolute; right: 40px; top: 90px; text-align: right;
    border-bottom: 1.5px solid var(--navy); padding: 0 0 3px 40px;
  }
  .person-name { color: var(--navy); font-weight: 700; font-size: 20px; letter-spacing: 0.5px; }
  .person-role { color: var(--text-blue); font-size: 12px; }
  .contact {
    position: absolute; left: 26px; top: 196px;
    border-top: 1.5px solid var(--navy); padding-top: 6px;
    color: var(--text-blue); font-size: 12.5px; line-height: 1.45;
  }
  .contact-row { display: flex; align-items: center; gap: 7px; }
  .contact-row svg { width: 10px; height: 10px; fill: var(--text-blue); }
  .contact-indent { padding-left: 17px; }
  .contact strong { font-weight: 700; }
</style>
</head>
<body>

  <section class="card card-back">
    <svg class="card-shapes" viewBox="0 0 540 310" preserveAspectRatio="none" aria-hidden="true">
      <polygon points="0,276 300,276 322,256 540,256 540,310 0,310" fill="var(--white)"/>
      <polygon points="322,256 540,214 540,256" fill="var(--navy)"/>
    </svg>
    <div class="back-mark">
      <div class="back-mark-dot"></div>
      <div class="back-mark-name">Korvel</div>
    </div>
    <p class="back-web">www.<strong>korvelpartsco</strong>.com</p>
  </section>

  <section class="card card-front">
    <svg class="card-shapes" viewBox="0 0 540 310" preserveAspectRatio="none" aria-hidden="true">
      <polygon points="0,300 390,292 390,298 0,310" fill="var(--brand-blue)"/>
      <polygon points="412,230 540,196 540,310 396,310" fill="var(--navy)"/>
      <line x1="220" y1="196" x2="330" y2="140" stroke="var(--navy)" stroke-width="1.5"/>
    </svg>
    <div class="brand">
      <div class="brand-dot"></div>
      <div class="brand-name">Korvel</div>
    </div>
    <div class="person">
      <div class="person-name">Marcus Hale</div>
      <div class="person-role">Director</div>
    </div>
    <div class="contact">
      <div class="contact-indent">P.O. Box 4410</div>
      <div class="contact-indent">Lansing, MI 48901</div>
      <div class="contact-row">
        <svg viewBox="0 0 10 10"><path d="M2 0.5 L4 2.5 L3 4 Q4.5 6 6 7 L7.5 6 L9.5 8 L8 9.5 Q3 9 0.5 2 Z"/></svg>
        +330 5812-3094
      </div>
      <div class="contact-row">
        <svg viewBox="0 0 10 10"><path d="M0 2 H10 V8 H0 Z M0.8 2.6 L5 5.6 L9.2 2.6 V3.4 L5 6.4 L0.8 3.4 Z" fill-rule="evenodd"/></svg>
        info@korvelpartsco.com
      </div>
      <div class="contact-row">
        <svg viewBox="0 0 10 10"><circle cx="5" cy="5" r="4.5"/></svg>
        www.<strong>korvelpartsco</strong>.com
      </div>
    </div>
  </section>

</body>
</html>
```